Insert card for anti-slip sticker

Product packaging should be inspired by the following
packaging and stand out at the same time: https://bxlo.example/7QwRtvk

The packaging is not packaging in the conventional sense, but rather a kind of insert card that can be opened.
This can also be found in the linked product.

On the front of the card: Product name (20 anti-slip strips), advantages of the product and a appealing picture with the product

Inside: Instructions for use and product tips

Back: Images with possible uses, company headquarters, email for contact purposes, note about positive evaluation on Veltora

```html
<!DOCTYPE html>
<html lang="en">
<head>
<meta charset="utf-8">
<title>Anti Slip Sticker – Insert Card</title>
<link rel="stylesheet" href="https://fonts.googleapis.com/css2?family=Marcellus&family=Questrial&display=swap">
<style>
  :root{
    --bg:#6d6e72;
    --paper:#fbfbfa;
    --gold:#c9a24e;
    --ink:#1b1b1b;
    --black:#141414;
    --label:#ffffff;
  }
  *{box-sizing:border-box;margin:0;padding:0}
  html,body{width:1200px;height:924px;overflow:hidden;background:var(--bg)}
  body{position:relative;font-family:"Questrial",sans-serif;color:var(--ink)}
  .panel-label{position:absolute;top:122px;font-family:"Marcellus",serif;font-size:8px;letter-spacing:.5px;color:var(--label)}
  .spread{position:absolute;top:138px;width:449px;height:672px;background:var(--paper);box-shadow:4px 6px 10px rgba(0,0,0,.35);overflow:hidden}
  .spread-outer{left:123px}
  .spread-inner{left:642px}
  .spread svg.art{position:absolute;inset:0}
  .abs{position:absolute}
  .count{display:flex;align-items:center;gap:7px;font-family:"Marcellus",serif;color:var(--gold)}
  .count .num{font-size:47px;line-height:1;letter-spacing:2px}
  .count .rule{width:1px;background:var(--ink);align-self:stretch;margin:3px 0}
  .count .words{font-size:15px;line-height:1.1;letter-spacing:.5px}
  .count .words span{display:block}
  .count .words .big{font-size:20px}
  .pill{border:1px solid var(--gold);border-radius:10px;font-size:8px;letter-spacing:.4px;text-align:center;color:var(--ink);background:#fff}
  .title{font-family:"Marcellus",serif;font-size:20px;font-weight:normal;letter-spacing:1px;color:var(--ink);white-space:nowrap}
  .contacts{list-style:none;color:#fff;font-size:8px}
  .contacts li{display:flex;align-items:center;gap:7px;height:18px}
  .contacts svg{width:11px;height:11px}
  .feature-label{font-family:"Marcellus",serif;font-size:8px;color:#fff;white-space:nowrap}
  .url{color:#fff;font-size:10.5px;width:221px;text-align:center}
  .uses{list-style:none;font-size:8.3px;line-height:12.4px;width:190px}
  .uses li{position:relative;padding-left:10px;margin-bottom:7px}
  .uses li::before,.specs li::before{content:"";position:absolute;left:0;top:3px;width:5px;height:5px;border:1px solid var(--gold);border-radius:50%}
  .specs-head{font-family:"Marcellus",serif;font-size:17px;font-weight:normal;color:var(--gold);letter-spacing:1px;white-space:nowrap}
  .specs{list-style:none;font-size:11.5px;line-height:19.5px}
  .specs li{position:relative;padding-left:16px}
  .specs li::before{top:6px;width:7px;height:7px}
  .step{font-size:8.8px;line-height:12.6px;width:94px}
  .step b{display:block;font-weight:normal;color:var(--gold);font-size:9.6px}
  .step-num{position:absolute;width:22px;height:22px;border-radius:50%;background:var(--black);border:1.5px solid #fff;color:#fff;font-size:10px;display:flex;align-items:center;justify-content:center}
</style>
</head>
<body>
  <span class="panel-label" style="left:136px">BACK</span>
  <span class="panel-label" style="left:402px">FRONT</span>
  <span class="panel-label" style="left:654px">INSIDE LEFT</span>
  <span class="panel-label" style="left:919px">INSIDE RIGHT</span>

  <section class="spread spread-outer">
    <svg class="art" width="449" height="672" viewBox="0 0 449 672">
      <defs>
        <linearGradient id="marble" x1="0" y1="0" x2="1" y2="1">
          <stop offset="0" stop-color="#ffffff"/><stop offset=".5" stop-color="#f1f1ef"/><stop offset="1" stop-color="#fafaf8"/>
        </linearGradient>
        <linearGradient id="showerPhoto" x1="0" y1="0" x2="0" y2="1">
          <stop offset="0" stop-color="#5f6063"/><stop offset=".45" stop-color="#a2a3a5"/><stop offset=".8" stop-color="#4a4b4d"/><stop offset="1" stop-color="#1d1d1e"/>
        </linearGradient>
        <linearGradient id="band" x1="0" y1="0" x2="1" y2="0">
          <stop offset="0" stop-color="#1a1a1a"/><stop offset=".5" stop-color="#303030"/><stop offset="1" stop-color="#121212"/>
        </linearGradient>
      </defs>
      <rect width="449" height="672" fill="url(#marble)"/>
      <line x1="228" y1="0" x2="228" y2="672" stroke="#d9d9d9" stroke-width="1"/>
      <g role="img" aria-label="Photo of legs standing under a running shower on anti-slip strips">
        <path d="M179,0 L449,0 L449,430 Q385,505 300,485 Q255,476 228,460 L228,70 Q210,28 179,0 Z" fill="url(#showerPhoto)"/>
        <path d="M300,0 L360,0 L350,470 L320,480 Z" fill="#b08a66" opacity=".5"/>
      </g>
      <path d="M179,0 Q300,190 449,225" fill="none" stroke="var(--gold)" stroke-width="2"/>
      <g role="img" aria-label="Photo of hands applying an anti-slip strip">
        <circle cx="58" cy="293" r="37" fill="#c9c6c2" stroke="var(--gold)" stroke-width="2"/>
      </g>
      <g role="img" aria-label="Photo of bare feet on anti-slip strips in a shower">
        <circle cx="122" cy="340" r="60" fill="#8f9093" stroke="var(--gold)" stroke-width="2"/>
      </g>
      <g role="img" aria-label="Photo of a transparent strip on a wooden step">
        <circle cx="168" cy="405" r="37" fill="#b89c78" stroke="var(--gold)" stroke-width="2"/>
      </g>
      <path d="M0,562 Q140,552 240,625 Q265,645 275,672 L0,672 Z" fill="#6f6f71"/>
      <path d="M0,570 Q140,566 228,640 Q245,657 250,672 L0,672 Z" fill="url(#band)"/>
      <path d="M228,618 Q330,590 449,598 L449,672 L228,672 Z" fill="url(#band)"/>
      <g fill="#111">
        <circle cx="265" cy="256" r="26" stroke="var(--gold)" stroke-width="1.5"/>
        <circle cx="265" cy="331" r="26" stroke="var(--gold)" stroke-width="1.5"/>
        <circle cx="265" cy="404" r="26" stroke="var(--gold)" stroke-width="1.5"/>
      </g>
      <g fill="none" stroke="#fff" stroke-width="2.2" stroke-linecap="round" stroke-linejoin="round">
        <path d="M253,257 L262,266 L279,246"/>
        <path d="M265,318 Q254,332 258,339 Q265,347 272,339 Q276,332 265,318 Z" fill="#fff"/>
        <path d="M252,414 L278,394 M270,394 L278,394 L278,402"/>
      </g>
    </svg>

    <div class="count abs" style="left:50px;top:168px">
      <span class="num">20</span><span class="rule"></span>
      <span class="words"><span>ANTI-SLIP</span><span class="big">STRIPS</span></span>
    </div>
    <h1 class="title abs" style="left:24px;top:483px">ANTI SLIP STICKER</h1>
    <div class="pill abs" style="left:33px;top:519px;width:162px;height:19px;line-height:17px">BATH / SHOWER / TUB / WET AREA</div>
    <ul class="contacts abs" style="left:15px;top:605px">
      <li><svg viewBox="0 0 12 12"><circle cx="6" cy="6" r="5.4" fill="none" stroke="var(--gold)"/><path d="M4,3.4 L5,3.4 L5.5,5 L4.8,5.5 Q5.4,6.8 6.5,7.3 L7,6.6 L8.6,7.1 L8.6,8.1 Q5,8.4 4,3.4Z" fill="var(--gold)"/></svg>010 555 0142</li>
      <li><svg viewBox="0 0 12 12"><circle cx="6" cy="6" r="5.4" fill="none" stroke="var(--gold)"/><rect x="3.3" y="4" width="5.4" height="4" fill="none" stroke="var(--gold)" stroke-width=".8"/><path d="M3.3,4 L6,6.2 L8.7,4" fill="none" stroke="var(--gold)" stroke-width=".8"/></svg>hello@gripstripe.example</li>
      <li><svg viewBox="0 0 12 12"><circle cx="6" cy="6" r="5.4" fill="none" stroke="var(--gold)"/><circle cx="6" cy="6" r="3" fill="none" stroke="var(--gold)" stroke-width=".8"/><path d="M3,6 H9 M6,3 V9" stroke="var(--gold)" stroke-width=".8"/></svg>www.gripstripe.example</li>
    </ul>

    <span class="feature-label abs" style="left:238px;top:286px">100% Non-Slip</span>
    <span class="feature-label abs" style="left:235px;top:362px">Water Repellent</span>
    <span class="feature-label abs" style="left:238px;top:434px">Easy Assembly</span>

    <div class="count abs" style="left:272px;top:520px">
      <span class="num" style="font-size:42px">20</span><span class="rule"></span>
      <span class="words"><span style="font-size:12.5px">ANTI-SLIP</span><span class="big" style="font-size:18px">STRIPS</span></span>
    </div>
    <div class="pill abs" style="left:245px;top:570px;width:182px;height:20px;line-height:18px">BATH / SHOWER / TUB / WET AREA</div>
    <div class="url abs" style="left:228px;top:645px">www.gripstripe.example</div>
  </section>

  <section class="spread spread-inner">
    <svg class="art" width="449" height="672" viewBox="0 0 449 672">
      <defs>
        <linearGradient id="marble2" x1="0" y1="0" x2="1" y2="1">
          <stop offset="0" stop-color="#ffffff"/><stop offset=".5" stop-color="#f0f0ee"/><stop offset="1" stop-color="#fafaf8"/>
        </linearGradient>
        <linearGradient id="bathPhoto" x1="0" y1="0" x2="1" y2="1">
          <stop offset="0" stop-color="#6b5239"/><stop offset=".5" stop-color="#b08a58"/><stop offset="1" stop-color="#c8a574"/>
        </linearGradient>
        <linearGradient id="feetPhoto" x1="0" y1="0" x2="0" y2="1">
          <stop offset="0" stop-color="#d7d7d7"/><stop offset="1" stop-color="#f4f4f4"/>
        </linearGradient>
        <linearGradient id="band2" x1="0" y1="0" x2="1" y2="0">
          <stop offset="0" stop-color="#9a9a9c"/><stop offset=".6" stop-color="#2a2a2a"/><stop offset="1" stop-color="#111"/>
        </linearGradient>
      </defs>
      <rect width="449" height="672" fill="url(#marble2)"/>
      <path d="M95,0 Q160,60 226,92 L226,0 Z" fill="#a9a9ab"/>
      <g role="img" aria-label="Photo of a wooden bathroom with a glass shower and strips on the floor">
        <path d="M226,0 L449,0 L449,256 Q390,282 336,280 Q270,276 226,241 Z" fill="url(#bathPhoto)"/>
        <circle cx="391" cy="222" r="45" fill="#c7a472" stroke="#fff" stroke-width="2.5"/>
      </g>
      <path d="M95,0 Q160,65 226,95 Q320,140 449,158" fill="none" stroke="var(--gold)" stroke-width="2"/>
      <line x1="226" y1="0" x2="226" y2="672" stroke="#d9d9d9"/>
      <path d="M0,502 Q150,520 226,640 L226,672 L0,672 Z" fill="#3a3a3c"/>
      <g role="img" aria-label="Photo of bare feet on a white shower tray with anti-slip strips">
        <path d="M0,515 Q150,535 226,655 L226,672 L0,672 Z" fill="url(#feetPhoto)"/>
      </g>
      <path d="M226,672 Q330,620 449,606 L449,672 Z" fill="url(#band2)"/>
      <path d="M226,662 Q330,612 449,600" fill="none" stroke="var(--gold)" stroke-width="2"/>
      <g role="img" aria-label="Photo of hands peeling a strip from its backing">
        <circle cx="290" cy="323" r="39" fill="#8a8783" stroke="var(--gold)" stroke-width="2"/>
      </g>
      <g role="img" aria-label="Photo of hands peeling the protective film">
        <circle cx="286" cy="436" r="39" fill="#9a8f86" stroke="var(--gold)" stroke-width="2"/>
      </g>
      <g role="img" aria-label="Photo of hands pressing a strip onto a surface">
        <circle cx="288" cy="555" r="39" fill="#7d7875" stroke="var(--gold)" stroke-width="2"/>
      </g>
    </svg>

    <div class="count abs" style="left:17px;top:93px">
      <span class="num" style="font-size:40px">20</span><span class="rule"></span>
      <span class="words"><span style="font-size:11.5px">ANTI-SLIP</span><span class="big" style="font-size:16px">STRIPS</span></span>
    </div>
    <div class="abs" style="left:17px;top:134px;width:176px;height:1px;background:var(--gold)"></div>
    <ul class="uses abs" style="left:19px;top:165px">
      <li>Non-slip strips, anti-slip stair steps.</li>
      <li>Corvina children's bath with shower, bath mat, wooden bathroom set, parts, child safety stairs, bath mat, black stair steps, anti-slip rubber mat, washing machine baby mat, bath accessory, children's bath mat.</li>
      <li>Children's non-slip transparent mat, baby bath anti-slip mat, bathroom accessories set.</li>
      <li>Anti-slip stair steps, adhesive tape for stair steps, tile, granite, stair steps, non-slip steps</li>
    </ul>
    <h2 class="specs-head abs" style="left:27px;top:368px">20 ANTI-SLIP STRIPS</h2>
    <ul class="specs abs" style="left:27px;top:400px">
      <li>Non-Slip Strips 45 x 2 cm</li>
      <li>Transparent Non-Slip</li>
      <li>Bath and Shower Stairs</li>
    </ul>

    <span class="step-num" style="left:309px;top:298px">1</span>
    <span class="step-num" style="left:311px;top:404px">2</span>
    <span class="step-num" style="left:309px;top:526px">3</span>
    <p class="step abs" style="left:349px;top:314px"><b>STEP 1</b>Self adhesive anti-slip strips</p>
    <p class="step abs" style="left:349px;top:421px"><b>STEP 2</b>Quick and easy to use: just peel and stick</p>
    <p class="step abs" style="left:349px;top:543px"><b>STEP 3</b>Perfect for bathrooms, stairs, decking, walkways, ramps...</p>
  </section>
</body>
</html>
```